Business Card Design needed for start up company Halvora

In need of a new business card designed for a start up company based in Sydney, Halvora is a new start up innovative Company, our mission it to make property accessible for everyday Australian and to become the leading Real Estate platform in Australia. We want it to be fresh and clean.

Industry/Entity Type

Financial

Contact Information for Business Card

Section for Name
Section for Title

HALVORA - The Strength of Pooling
Mobile:
Direct:

Font styles to use
Sans Serif

Colors
33a6d7
0692cd
0255a3
ffffff

Requirements
Must have
• Logo, all business card details

```html
<!DOCTYPE html>
<html lang="en">
<head>
<meta charset="utf-8">
<title>Halvora Business Card</title>
<link href="https://fonts.googleapis.com/css2?family=Open+Sans:wght@400;600;700&display=swap" rel="stylesheet">
<style>
  :root {
    --sky: #33a6d7;
    --ocean: #0692cd;
    --navy: #0255a3;
    --deep-navy: #1a3d7c;
    --white: #ffffff;
    --ink-grey: #4a4f57;
    --backdrop: #e9ebee;
  }
  * { margin: 0; padding: 0; box-sizing: border-box; }
  html, body {
    width: 1200px; height: 960px; overflow: hidden;
    background: var(--backdrop);
    font-family: "Open Sans", Arial, sans-serif;
  }
  .canvas {
    width: 1200px; height: 960px;
    display: flex; flex-direction: column; align-items: center; justify-content: center;
    gap: 56px;
  }
  .card {
    width: 700px; height: 400px;
    position: relative; overflow: hidden;
    box-shadow: 0 6px 20px rgba(0,0,0,.15);
  }
  .wordmark {
    font-family: "Open Sans", Arial, sans-serif; font-weight: 700;
    letter-spacing: 1px; line-height: 1; white-space: nowrap;
  }
  /* Back */
  .card-back {
    background: linear-gradient(135deg, var(--sky), var(--ocean));
    display: flex; flex-direction: column; align-items: center; justify-content: center;
  }
  .card-back .wordmark { color: var(--white); font-size: 68px; }
  .tagline {
    margin-top: 48px; color: var(--white); font-size: 15px; letter-spacing: .3px;
  }
  /* Front */
  .card-front { background: var(--white); }
  .brand-band {
    position: absolute; left: 0; top: 48px; width: 40px; height: 84px;
    background: var(--deep-navy);
  }
  .card-front .wordmark {
    position: absolute; left: 64px; top: 58px;
    color: var(--deep-navy); font-size: 62px;
  }
  .contact {
    position: absolute; right: 42px; bottom: 34px; text-align: right;
    color: var(--ink-grey); font-size: 15px; line-height: 1.4;
  }
  .person-name { color: var(--deep-navy); font-weight: 700; font-size: 19px; letter-spacing: .5px; }
  .person-title { color: var(--ocean); font-weight: 600; font-size: 16px; margin-bottom: 8px; letter-spacing: .5px; }
  .address { margin-bottom: 6px; }
  .contact-line { display: flex; align-items: center; justify-content: flex-end; gap: 8px; }
  .contact-line svg { width: 14px; height: 14px; fill: var(--deep-navy); flex: none; }
</style>
</head>
<body>
<main class="canvas">
  <section class="card card-back" aria-label="Card back">
    <p class="wordmark">HALVORA</p>
    <p class="tagline">The Strength of Pooling</p>
  </section>

  <section class="card card-front" aria-label="Card front">
    <div class="brand-band"></div>
    <p class="wordmark">HALVORA</p>

    <div class="contact">
      <p class="person-name">MARA ELLISON</p>
      <p class="person-title">CEO/FOUNDER</p>
      <p class="address">214 Harbour Row<br>Sydney, NSW 2000</p>
      <p class="contact-line">02 9184 6620
        <svg viewBox="0 0 16 16" aria-hidden="true"><path d="M2 5c0-2 2-3 6-3s6 1 6 3v1h-3V5H5v1H2zM4 8h8l2 6H2z"/></svg></p>
      <p class="contact-line">0412 775 019
        <svg viewBox="0 0 16 16" aria-hidden="true"><path d="M4 1h8v14H4zM5.5 3v9h5V3zM7 13h2v1H7z"/></svg></p>
      <p class="contact-line">mara@halvora.com
        <svg viewBox="0 0 16 16" aria-hidden="true"><path d="M1 3h14v10H1zM2 4.5v.5l6 4 6-4v-.5z"/></svg></p>
      <p class="contact-line">www.halvora.com
        <svg viewBox="0 0 16 16" aria-hidden="true"><circle cx="8" cy="8" r="7"/></svg></p>
    </div>
  </section>
</main>
</body>
</html>
```